Professional & attention grabbing.

A business card design, front and back. I already have a logo I will attach, but I am open to something new as well.
Things to include:
Name:
Title:
Phone:
Email:
Wanting something that is professional but attention grabbing.
Also we do a lot of work using drones on natural gas pipelines (leading the future)if you want to include any of that. I'm open to ideas.
Target Market(s)
Natural gas transmission industry / greenhouse gas mitigation industry
Industry/Entity Type
Business
Colors
Designer to choose colors to be used in the design.
Look and feel
Each slider illustrates characteristics of the customer's brand and the style your logo design should communicate.

```html
<!DOCTYPE html>
<html lang="en">
<head>
<meta charset="UTF-8">
<title>KV Field Surveys — Business Card</title>
<link rel="stylesheet" href="https://fonts.googleapis.com/css2?family=Open+Sans:wght@400;700&family=Quicksand:wght@500&display=swap">
<style>
  :root {
    --ink: #37373b;
    --signal-red: #be1e26;
    --paper: #ffffff;
    --backdrop: #ececec;
  }
  * { margin: 0; padding: 0; box-sizing: border-box; }
  html, body {
    width: 1200px;
    height: 1135px;
    overflow: hidden;
    background: var(--backdrop);
  }
  .canvas {
    position: relative;
    width: 1200px;
    height: 1135px;
  }
  .card {
    position: absolute;
    width: 680px;
    height: 406px;
    background: var(--paper);
    box-shadow: 0 10px 24px rgba(0, 0, 0, 0.18);
    overflow: hidden;
  }
  .card--front { left: 234px; top: 90px; }
  .card--back  { left: 239px; top: 625px; }
  .card__shapes {
    position: absolute;
    inset: 0;
    width: 100%;
    height: 100%;
  }
  .icon {
    position: absolute;
    fill: var(--signal-red);
  }
  .icon--light { fill: var(--paper); }
  .holder-name {
    position: absolute;
    left: 82px;
    top: 56px;
    font-family: "Open Sans", sans-serif;
    font-weight: 700;
    font-size: 28px;
    color: var(--paper);
    line-height: 1;
  }
  .holder-title {
    position: absolute;
    left: 82px;
    top: 92px;
    font-family: "Quicksand", sans-serif;
    font-weight: 500;
    font-size: 16px;
    color: var(--paper);
    line-height: 1;
  }
  .contact {
    position: absolute;
    left: 82px;
    font-family: "Quicksand", sans-serif;
    font-weight: 500;
    font-size: 16px;
    color: var(--paper);
    line-height: 1;
  }
  .contact--phone { top: 304px; }
  .contact--email { top: 362px; }
  .brand {
    position: absolute;
    display: flex;
    align-items: center;
    white-space: nowrap;
  }
  .brand__square {
    background: var(--signal-red);
    flex: none;
  }
  .brand__name {
    font-family: "Open Sans", sans-serif;
    font-weight: 700;
    color: var(--ink);
    line-height: 1;
  }
  .brand--front { left: 446px; top: 186px; gap: 10px; }
  .brand--front .brand__square { width: 26px; height: 26px; }
  .brand--front .brand__name { font-size: 20px; }
  .brand--back { left: 140px; top: 180px; gap: 16px; }
  .brand--back .brand__square { width: 46px; height: 46px; }
  .brand--back .brand__name { font-size: 38px; }
</style>
</head>
<body>
<main class="canvas">

  <section class="card card--front" aria-label="Card front">
    <svg class="card__shapes" viewBox="0 0 680 406" aria-hidden="true">
      <polygon fill="var(--ink)" points="0,0 425,0 354,406 0,406"/>
      <polygon fill="var(--signal-red)" points="425,0 431,0 376,406 354,406"/>
      <path fill="var(--signal-red)" d="M0 0 H25 V138 C25 160 75 158 75 192 V406 H0 Z"/>
    </svg>

    <svg class="icon" style="left:44px; top:62px;" width="22" height="26" viewBox="0 0 22 26" aria-hidden="true">
      <circle cx="11" cy="7" r="6.5"/>
      <path d="M0 26 C0 16 4 14 11 14 C18 14 22 16 22 26 Z"/>
    </svg>
    <h1 class="holder-name">Your Name</h1>
    <p class="holder-title">Title</p>

    <svg class="icon icon--light" style="left:46px; top:302px;" width="14" height="20" viewBox="0 0 14 20" aria-hidden="true">
      <path d="M3 0 L6 1 L6.5 6 L4.5 7.5 C5 10.5 6.5 13 8.5 14.5 L10.5 13 L14 16 L12 19.5 C6 19 1 11 1 3 Z"/>
    </svg>
    <p class="contact contact--phone">555010234</p>

    <svg class="icon icon--light" style="left:45px; top:365px;" width="17" height="12" viewBox="0 0 17 12" aria-hidden="true">
      <path d="M0 0 H17 V12 H0 Z M1.5 1.5 L8.5 7 L15.5 1.5 Z" fill-rule="evenodd"/>
    </svg>
    <p class="contact contact--email">name@kvfield.com</p>

    <div class="brand brand--front">
      <span class="brand__square"></span>
      <span class="brand__name">KV Field Surveys</span>
    </div>
  </section>

  <section class="card card--back" aria-label="Card back">
    <svg class="card__shapes" viewBox="0 0 680 406" aria-hidden="true">
      <polygon fill="var(--ink)" points="0,0 88,0 34,406 0,406"/>
      <polygon fill="var(--signal-red)" points="88,0 105,0 34,406"/>
      <polygon fill="var(--signal-red)" points="650,0 661,0 608,406 592,406"/>
      <polygon fill="var(--ink)" points="661,0 680,0 680,406 608,406"/>
    </svg>

    <div class="brand brand--back">
      <span class="brand__square"></span>
      <span class="brand__name">KV Field Surveys</span>
    </div>
  </section>

</main>
</body>
</html>
```